Business card

We need a business card design for our company based in Auckland , New Zealand called 'Ridge + Studio Ltd'. We provide architectural services. We would like to see designs that use the max. three colours (such as white, black, grey) The final design should communicate financial safety and growth."
Also I will provide our company logo. I would like to the logo to be embeded onto our business card.

Target Market(s)

new residential house, alteration & addition & light commericila design & drafting service

Industry/Entity Type

Architecture

Contact Information for Business Card

Company name: ridge + studio Ltd.
Name: Mark Delford
Job title: architectural designer & Design LBP
email address: mark@rplusd.co.nz
mobile number: 02 5163 2290
web site: www.rplusd.co.nz

Requirements
Must have
• My project must have..
• - embeded logo (attached company logo)
• I don't have a bigger version for our company logo, but I have one old one, so you can remove the word from it)
• - insert the attached small BKTW logo & LBP logo
• - creative, simple and clear business card.
• - Max. three colours
Nice to have
• - Here are the samples I would like to share with you: http://www.plimvora.com/blog/minimalistic-business-card-designs/
• I would like to have my business card like one of the creation.
Should not have
• TBA

```html
<!DOCTYPE html>
<html lang="en">
<head>
<meta charset="utf-8">
<title>Ridge + Studio Ltd — Business Card</title>
<link href="https://fonts.googleapis.com/css2?family=Montserrat:wght@400;500;600;700&display=swap" rel="stylesheet">
<style>
  :root {
    --stage: #2a2a2a;
    --ink: #111111;
    --paper: #ffffff;
    --grey: #8a8a8a;
    --grey-dark: #555555;
    --grey-soft: #bdbdbd;
  }
  * { box-sizing: border-box; margin: 0; padding: 0; }
  html, body { width: 1200px; height: 900px; overflow: hidden; }
  body {
    background: var(--stage);
    font-family: "Montserrat", sans-serif;
    position: relative;
  }
  .card {
    position: absolute;
    width: 540px;
    height: 310px;
    border-radius: 22px;
    overflow: hidden;
  }
  /* Front */
  .card-front { left: 110px; top: 130px; background: var(--ink); color: var(--paper); }
  .front-mark {
    position: absolute; left: 150px; top: 40px;
    width: 150px; height: 150px; border-radius: 50%;
    border: 10px solid var(--paper);
  }
  .front-name {
    position: absolute; left: 40px; top: 200px;
    font-size: 25px; font-weight: 600; letter-spacing: 0.3px;
  }
  .front-rule {
    position: absolute; left: 40px; right: 40px; top: 190px;
    height: 1px; background: var(--grey-dark);
  }
  .front-web {
    position: absolute; left: 40px; bottom: 32px;
    font-size: 17px; font-weight: 500; color: var(--grey-soft);
  }
  .member {
    position: absolute; right: 130px; top: 120px;
    text-align: left;
  }
  .member-name { font-size: 30px; font-weight: 700; color: var(--grey-dark); letter-spacing: 1px; }
  .member-role { font-size: 12px; font-weight: 600; line-height: 1.2; color: var(--grey-soft); margin-top: 2px; }
  .badge {
    position: absolute; right: 30px; top: 110px;
    width: 80px; height: 80px; border-radius: 50%;
    background: var(--paper); border: 6px solid var(--grey-dark);
  }
  /* Back */
  .card-back { left: 550px; top: 460px; background: var(--paper); color: var(--ink); }
  .brand {
    position: absolute; left: 40px; top: 70px; width: 220px;
    display: flex; flex-direction: column; align-items: center; gap: 16px;
  }
  .brand-mark {
    width: 130px; height: 130px; border-radius: 50%;
    border: 9px solid var(--ink);
  }
  .brand-name { font-size: 17px; font-weight: 600; color: var(--ink); }
  .divider {
    position: absolute; left: 290px; top: 45px; bottom: 45px;
    width: 1px; background: var(--ink);
  }
  .details { position: absolute; left: 315px; top: 70px; }
  .person { font-size: 24px; font-weight: 700; letter-spacing: 0.5px; }
  .role { font-size: 14px; color: var(--grey); line-height: 1.3; margin-top: 4px; }
  .contacts { list-style: none; margin-top: 12px; }
  .contacts li {
    display: flex; align-items: center; gap: 8px;
    font-size: 14px; font-weight: 500; line-height: 1.6;
  }
  .contacts svg { width: 13px; height: 13px; flex: none; }
</style>
</head>
<body>
  <section class="card card-front">
    <div class="front-mark"></div>
    <div class="front-rule"></div>
    <div class="front-name">Ridge + Studio Ltd</div>
    <div class="front-web">www.rplusd.co.nz</div>
    <div class="member">
      <div class="member-name">BKTW</div>
      <div class="member-role">Professional<br>Member</div>
    </div>
    <div class="badge" role="img" aria-label="Licensed practitioner badge"></div>
  </section>

  <section class="card card-back">
    <div class="brand">
      <div class="brand-mark"></div>
      <div class="brand-name">Ridge + Studio Ltd</div>
    </div>
    <div class="divider"></div>
    <div class="details">
      <div class="person">MARK DELFORD</div>
      <div class="role">Architectural designer<br>&amp; Design LBP</div>
      <ul class="contacts">
        <li>
          <svg viewBox="0 0 16 16" aria-hidden="true"><path d="M3 1.5l3 .5 1 3-2 1.5a9 9 0 0 0 4.5 4.5L11 9l3 1 .5 3-2 1.5C7 14 2 9 1.5 3.5z" fill="#555"/></svg>
          02 5163 2290
        </li>
        <li>
          <svg viewBox="0 0 16 16" aria-hidden="true"><rect x="1.5" y="3.5" width="13" height="9" fill="none" stroke="#555" stroke-width="1.4"/><path d="M1.5 3.5L8 9l6.5-5.5" fill="none" stroke="#555" stroke-width="1.4"/></svg>
          mark@rplusd.co.nz
        </li>
        <li>
          <svg viewBox="0 0 16 16" aria-hidden="true"><circle cx="8" cy="8" r="6.5" fill="none" stroke="#555" stroke-width="1.3"/><ellipse cx="8" cy="8" rx="2.8" ry="6.5" fill="none" stroke="#555" stroke-width="1.1"/><path d="M1.5 8h13" stroke="#555" stroke-width="1.1"/></svg>
          www.rplusd.co.nz
        </li>
      </ul>
    </div>
  </section>
</body>
</html>
```